Detail Shop Business card design

i need a business card design for my new detailing company called 'Brisk's Polish Works'. i want an all black and white design . simple, direct and to the point. i want the designer to choose a fitting font to match the logothe front should have logo, address, phone and email and the back side should have a slogan and text indicating that we offer services on anything including cars, trucks, motorcycles and RVs. slogan will read "we take pride in your ride"
maybe also very small on the back side the IG icon with Brisks_Polish_Works

phone 208.417.6352
address 3847 E Larkin Ave
Spokane WA 99214
email: BrisksPolish@mailvexo.com

Target Market(s)

all ages , auto enthusiasts

Industry/Entity Type

Automotive

Contact Information for Business Card

the front should have logo, address, phone and email and the back side should have a slogan and text indicating that we offer services on anything including cars, trucks, motorcycles and RVs. slogan will read "we take pride in your ride"

phone 208.417.6352
address 3847 E Larkin Ave
Spokane WA 99214

Colors
000000
ffffff

Requirements
Must have
• bold font and very simple design with good spacing
Nice to have
• anything creative from the designer indicating we service any types of vehicles
Should not have
• any colors ,

```html
<!DOCTYPE html>
<html lang="en">
<head>
<meta charset="utf-8">
<title>Brisk's Polish Works – Business Card</title>
<link href="https://fonts.googleapis.com/css2?family=Lato:wght@300;400;700&display=swap" rel="stylesheet">
<style>
  :root {
    --page: #1c1c1c;
    --card: #0d0d0d;
    --card-edge: #1a1a1a;
    --ink: #ffffff;
    --ink-soft: #d9d9d9;
    --rule: #6a6a6a;
    --ghost-a: rgba(255,255,255,0.07);
    --ghost-b: rgba(255,255,255,0);
  }
  * { box-sizing: border-box; margin: 0; padding: 0; }
  html, body {
    width: 1200px; height: 900px; overflow: hidden;
    background: var(--page);
    font-family: "Lato", Arial, sans-serif;
    color: var(--ink);
  }
  .canvas {
    width: 1200px; height: 900px;
    display: flex; flex-direction: column; align-items: center; justify-content: center;
    gap: 50px;
  }
  .card {
    position: relative;
    width: 560px; height: 320px;
    background: linear-gradient(160deg, var(--card-edge), var(--card) 60%);
    border-radius: 18px;
    overflow: hidden;
    box-shadow: 0 18px 40px rgba(0,0,0,0.55);
  }

  /* Back */
  .back__art {
    position: absolute; left: 60px; top: 110px; width: 330px; height: 170px;
    border-radius: 80px 60px 40px 80px;
    background: radial-gradient(ellipse at 40% 60%, var(--ghost-a), var(--ghost-b) 70%);
  }
  .back__content {
    position: absolute; inset: 0;
    display: flex; flex-direction: column; align-items: center; justify-content: center;
    text-align: center;
  }
  .back__services {
    font-weight: 300; font-size: 19px; line-height: 1.5; color: var(--ink-soft);
  }
  .back__rule {
    width: 300px; height: 1px; background: var(--rule); margin: 26px 0 18px;
  }
  .back__slogan {
    font-weight: 400; font-size: 19px; letter-spacing: 0.04em;
  }

  /* Front */
  .front__art {
    position: absolute; left: 0; top: 70px; width: 300px; height: 90px;
    background: linear-gradient(90deg, var(--ghost-b), var(--ghost-a) 55%, var(--ghost-b));
    border-radius: 0 50px 50px 0;
  }
  .front__brand {
    position: absolute; right: 40px; top: 52px;
    display: flex; align-items: center; gap: 12px;
  }
  .front__brand-dot {
    width: 30px; height: 30px; border-radius: 50%; background: var(--ink);
  }
  .front__brand-name {
    font-weight: 700; font-size: 24px; letter-spacing: 0.02em;
  }
  .front__rule-top {
    position: absolute; right: 30px; top: 112px; width: 250px; height: 1px; background: var(--rule);
  }
  .front__address {
    position: absolute; right: 30px; top: 128px;
    text-align: right; font-size: 15px; line-height: 1.35; color: var(--ink-soft);
  }
  .front__contacts {
    position: absolute; left: 30px; bottom: 30px;
    font-size: 16px; line-height: 1.5;
  }
  .contact { display: flex; align-items: center; gap: 8px; }
  .contact--handle { margin-bottom: 10px; font-size: 17px; }
  .contact__dot {
    width: 18px; height: 18px; border-radius: 50%; background: var(--ink);
  }
  .contact__icon { width: 15px; height: 15px; fill: var(--ink); }
  .front__rule-mid {
    position: absolute; left: 215px; bottom: 102px; width: 190px; height: 1px; background: var(--rule);
  }
</style>
</head>
<body>
<main class="canvas">

  <section class="card card--back" aria-label="Card back">
    <div class="back__art" role="img" aria-label="Faint hot rod car illustration"></div>
    <div class="back__content">
      <p class="back__services">We offer services on<br>anything including<br>cars, trucks, motorcycles<br>and RVs.</p>
      <div class="back__rule"></div>
      <p class="back__slogan">WE TAKE PRIDE IN YOUR RIDE</p>
    </div>
  </section>

  <section class="card card--front" aria-label="Card front">
    <div class="front__art" role="img" aria-label="Faint hot rod car illustration"></div>
    <div class="front__brand">
      <span class="front__brand-dot"></span>
      <span class="front__brand-name">Brisk's Polish Works</span>
    </div>
    <div class="front__rule-top"></div>
    <p class="front__address">3847 E Larkin Ave<br>Spokane WA 99214</p>
    <div class="front__rule-mid"></div>
    <div class="front__contacts">
      <p class="contact contact--handle"><span class="contact__dot"></span>Brisks_Polish_Works</p>
      <p class="contact">
        <svg class="contact__icon" viewBox="0 0 16 16" aria-hidden="true"><path d="M3 1h3l1 4-2 1c1 2 3 4 5 5l1-2 4 1v3c0 1-1 2-2 2C7 15 1 9 1 3c0-1 1-2 2-2z"/></svg>
        208.417.6352
      </p>
      <p class="contact">
        <svg class="contact__icon" viewBox="0 0 16 16" aria-hidden="true"><path d="M1 3h14v10H1z M2 4l6 5 6-5" fill="none" stroke="#fff" stroke-width="1.5"/></svg>
        BrisksPolish@mailvexo.com
      </p>
    </div>
  </section>

</main>
</body>
</html>
```